Luxury Wine Label for New Startup Winery

We need a wine label for our new winery startup. We have worked with a local designer but do not feel the resulting label / logo have the elevation required to present our brand as a luxury wine. Our winery is called "Quailbrook Vineyards" and we are focused on extremely high quality hand crafted artisan and estate wines from the Pacific Northwest.
We would like to see designs that utilize a tree line, or other imagery that represents the "Quailbrook" part of our company name. Another interesting feature could be wood grain.
A logo will be required based on your design so please design with this in mind:
This logo should be consistent with the wine bottle label design, and should be representative of our high end exclusive wine while giving a sense of place (Oregon/ Pacific Northwest.)
I will supply an image of the design we received from our local designer, PLEASE NOTE: in general we do like wood grain and tree line concepts but feel the execution was poorly done.
ATTN: Logo design should be suitable for use on: Bottles (Red wine/rose/white wine), Bussiness cards, vehicle signage, business signage, etc
P.S.:
If you have a design that is not outside the box we are still interested in seeing it.
Label is for a burgundy style bottle with a label height of 3.5 - 4" and a width of 3.5-4"
any label <= 4"x4" and >=3.5"x3.5" will be acceptable:
HOWEVER Width should be greater than or equal to height due to the bottle format
Target Market(s)
Wine enthusiasts with adequate discretionary budgets to afford $100 bottles of wine.
Industry/Entity Type
Wine / Winery
Requirements
Must have
- A sense of luxury, a feel of exclusivity, and a theme consistent with our product and brand name
Nice to have
- Tree line, wood grain or other wood themes. Serif fonts
Should not have
- anything cheesy, off topic, hard to read script fonts or anything that makes the label hard to read from a few feet away or too busy

```html
<!DOCTYPE html>
<html lang="en">
<head>
<meta charset="utf-8">
<title>Quailbrook Vineyards — Rosé Label</title>
<link href="https://fonts.googleapis.com/css2?family=Cinzel:wght@700&family=Oswald:wght@300;400&display=swap" rel="stylesheet">
<style>
  :root {
    --page: #ffffff;
    --label-cream: #f9f5ea;
    --band-pink: #f1ab9b;
    --band-line: #e8746a;
    --wine-red: #c9473b;
    --bark-brown: #4a332c;
    --ink: #3a2a25;
    --branch-tone: #d9d3bd;
  }
  * { margin: 0; padding: 0; box-sizing: border-box; }
  html, body {
    width: 1200px; height: 1200px; overflow: hidden;
    background: var(--page);
  }
  .canvas { position: relative; width: 1200px; height: 1200px; }
  .label {
    position: absolute; left: 50px; top: 203px;
    width: 1100px; height: 793px;
    background: var(--label-cream);
    border-radius: 15px;
    overflow: hidden;
  }
  .label__band {
    position: absolute; left: 0; top: 442px;
    width: 100%; height: 197px;
    background: var(--band-pink);
    border-top: 4px solid var(--band-line);
  }
  .label__branches {
    position: absolute; left: 566px; top: 0;
    width: 534px; height: 100%;
    background: linear-gradient(160deg, rgba(217,211,189,0) 10%, rgba(217,211,189,0.35) 55%, rgba(217,211,189,0.5) 100%);
  }
  .brand {
    position: absolute; left: 168px; top: 117px;
    display: flex; align-items: flex-start; gap: 19px;
  }
  .brand__mark {
    width: 57px; height: 57px; margin-top: 14px;
    background: var(--bark-brown);
  }
  .brand__name {
    font-family: "Cinzel", serif; font-weight: 700;
    font-size: 40px; line-height: 37px; letter-spacing: 2px;
    color: var(--bark-brown);
  }
  .brand__region {
    font-family: "Oswald", sans-serif; font-weight: 300;
    font-size: 22px; letter-spacing: 0.5px;
    color: var(--wine-red);
    margin-top: 6px;
  }
  .wine-info {
    position: absolute; left: 244px; top: 480px;
  }
  .wine-info__tagline {
    font-family: "Oswald", sans-serif; font-weight: 400;
    font-size: 17px; letter-spacing: 0.3px;
    color: var(--ink);
  }
  .wine-info__varietal {
    font-family: "Cinzel", serif; font-weight: 700;
    font-size: 42px; letter-spacing: 2px;
    color: var(--wine-red);
    margin-top: 14px; line-height: 1;
  }
  .wine-info__specs {
    font-family: "Oswald", sans-serif; font-weight: 400;
    font-size: 17px; color: var(--ink);
    margin-top: 18px;
    display: flex; align-items: baseline; gap: 10px;
  }
  .wine-info__vintage { font-size: 26px; }
</style>
</head>
<body>
<div class="canvas">
  <div class="label">
    <div class="label__band"></div>
    <div class="label__branches" role="img" aria-label="Faint bare tree branches with small perched birds"></div>

    <div class="brand">
      <div class="brand__mark"></div>
      <div>
        <div class="brand__name">Quailbrook<br>Vineyards</div>
        <div class="brand__region">WILLAMETTE VALLEY, OREGON</div>
      </div>
    </div>

    <div class="wine-info">
      <div class="wine-info__tagline">HAND-CRAFTED ARTISAN ESTATE WINES FROM THE PACIFIC NORTHWEST</div>
      <div class="wine-info__varietal">Rosé</div>
      <div class="wine-info__specs">
        <span>750 ml</span><span>/</span>
        <span class="wine-info__vintage">2024</span><span>/</span>
        <span>13% Alc. Vol.</span>
      </div>
    </div>
  </div>
</div>
</body>
</html>
```